Business card design needed

I need a business card design for a dog walking, dog minding and dog training business. Please refer to my website for the basic company colours and fonts I'm after. Planning on a double sided card, so all information doesn't need to be on the 'front' side.
Cheers

Industry/Entity Type

Dog Training

Contact Information for Business Card

Bramble Paws - gathering hounds
Rua 0498376214
bramblepaws.com.au
-walking
-holiday stays
-onsite care
-training and behavioural consultations

```html
<!DOCTYPE html>
<html lang="en">
<head>
<meta charset="utf-8">
<title>Bramble Paws – Business Card</title>
<link href="https://fonts.googleapis.com/css2?family=Exo+2:ital,wght@0,300;0,400;0,600;0,700;1,300&display=swap" rel="stylesheet">
<style>
  :root {
    --backdrop: #d8d3cb;
    --card-light: #f4f4f2;
    --card-dark: #3c3d3f;
    --ink-dark: #2b2b2b;
    --ink-soft: #555555;
    --ink-light: #ececec;
    --accent: #c8441b;
    --figure-light: #dcdcda;
    --figure-dark: #55575a;
  }
  * { box-sizing: border-box; margin: 0; padding: 0; }
  html, body {
    width: 1200px;
    height: 720px;
    overflow: hidden;
  }
  body {
    background: var(--backdrop);
    font-family: "Exo 2", sans-serif;
    position: relative;
  }
  .card {
    position: absolute;
    top: 205px;
    width: 500px;
    height: 305px;
    border-radius: 3px;
    box-shadow: 0 6px 18px rgba(0,0,0,0.18);
    overflow: hidden;
  }
  .card--front { left: 70px; background: var(--card-light); color: var(--ink-dark); }
  .card--back  { left: 630px; background: var(--card-dark); color: var(--ink-light); }

  .contact {
    position: absolute;
    top: 26px;
    right: 28px;
    text-align: right;
  }
  .contact__line { font-size: 22px; font-weight: 400; letter-spacing: 0.5px; }
  .contact__name { font-weight: 700; margin-right: 6px; }
  .contact__area {
    font-size: 13.5px;
    font-weight: 300;
    font-style: italic;
    color: var(--ink-soft);
    margin-top: 4px;
  }

  .dog-figure {
    position: absolute;
    border-radius: 4px;
  }
  .card--front .dog-figure {
    left: 30px; top: 128px; width: 120px; height: 150px;
    background: linear-gradient(180deg, var(--figure-light), #e9e9e7);
  }
  .card--back .dog-figure {
    left: 30px; top: 58px; width: 140px; height: 185px;
    background: linear-gradient(180deg, var(--figure-dark), #47494b);
  }

  .brand {
    position: absolute;
  }
  .card--front .brand { left: 162px; top: 188px; }
  .card--back  .brand { left: 185px; top: 112px; }
  .brand__row { display: flex; align-items: center; gap: 10px; }
  .brand__dot {
    width: 14px; height: 14px; border-radius: 50%;
    background: var(--accent);
    flex: none;
  }
  .brand__name {
    font-size: 40px;
    font-weight: 300;
    letter-spacing: 1.5px;
    line-height: 1;
    text-transform: uppercase;
  }
  .card--front .brand__name { color: var(--ink-dark); }
  .card--back  .brand__name { color: var(--ink-light); }
  .brand__tagline {
    font-size: 19px;
    font-weight: 300;
    margin-top: 4px;
    margin-left: 24px;
  }
  .card--front .brand__tagline { color: var(--ink-soft); }
  .card--back  .brand__tagline { color: #d0d0d0; }

  .ethos {
    position: absolute;
    top: 26px;
    right: 26px;
    width: 250px;
    text-align: right;
    font-size: 12.5px;
    font-weight: 300;
    line-height: 1.45;
    color: #d6d6d6;
  }
  .ethos strong { font-weight: 600; color: var(--ink-light); }
</style>
</head>
<body>

  <section class="card card--front" aria-label="Business card front">
    <div class="contact">
      <p class="contact__line"><span class="contact__name">Rua</span>0498 376 214</p>
      <p class="contact__area">servicing the inner suburbs of Melbourne</p>
    </div>
    <div class="dog-figure" role="img" aria-label="Line illustration of a standing dog on an orange lead"></div>
    <div class="brand">
      <div class="brand__row">
        <span class="brand__dot"></span>
        <span class="brand__name">Bramble Paws</span>
      </div>
      <p class="brand__tagline">gathering hounds</p>
    </div>
  </section>

  <section class="card card--back" aria-label="Business card back">
    <p class="ethos">We’re about a <strong>good balance</strong> of <strong>fun, exercise, proper stimulation</strong> and <strong>reinforcing good habits</strong> and <strong>canine manners</strong></p>
    <div class="dog-figure" role="img" aria-label="Line illustration of a standing dog on an orange lead"></div>
    <div class="brand">
      <div class="brand__row">
        <span class="brand__dot"></span>
        <span class="brand__name">Bramble Paws</span>
      </div>
      <p class="brand__tagline">gathering hounds</p>
    </div>
  </section>

</body>
</html>
```